To design a brand identity that is simple and creative with 'Corvane' as the brand name, I like modern simple fonts like helvetica neue, I want to print both sides of the card, I am open to dark front and white back, but the design needs to transfer well to letter heads and email signatures, I am looking for sophisticated and elegant, but open minded about clever and off the wall, I do not do 'boring' Corvane Ventures is the mother company for a small group, specialising in Management & consulting, Software development and construction, we have a high level of integrity, we are transparent and accountable for what we do. my images are provided as a guide only, Im not expecting them to be just copied, Im looking for a creator and passionate thinker, who will put life into their work.

Target Market(s)

usually business minded people who are looking for something different in me, such as leadership, confidence and focus with thinking that is per haps a little outside the box..

Industry/Entity Type

Construction

Requirements
Must have
• clean, minmalistic
Nice to have
• custom logo
Should not have
• boring, traditional

```html
<!DOCTYPE html>
<html lang="en">
<head>
<meta charset="utf-8">
<title>Corvane – Business Cards</title>
<link rel="stylesheet" href="https://fonts.googleapis.com/css2?family=Open+Sans:ital,wght@0,300;0,400;0,600;0,700;1,400&display=swap">
<style>
  :root {
    --stage: #e4e5e8;
    --card-dark: #2a2627;
    --card-light: #ffffff;
    --brand-orange: #e8562a;
    --text-light: #f4f4f4;
    --text-muted: #8d8a8b;
    --grad-yellow: #f6b21c;
    --grad-red: #e5322d;
    --grad-purple: #8e2f6e;
    --grad-teal: #1f9e88;
  }
  * { margin: 0; padding: 0; box-sizing: border-box; }
  html, body {
    width: 1200px; height: 987px; overflow: hidden;
    background: var(--stage);
    font-family: "Open Sans", "Helvetica Neue", Arial, sans-serif;
  }
  .stage { position: relative; width: 1200px; height: 987px; }

  .card {
    position: absolute;
    width: 700px; height: 400px;
    border-radius: 30px;
    overflow: hidden;
    box-shadow: 0 14px 30px rgba(0,0,0,.18);
  }

  /* Back card */
  .card--back { left: 440px; top: 70px; background: var(--card-light); }
  .back__wordmark {
    position: absolute; left: 0; right: 0; top: 70px;
    text-align: center;
    font-weight: 300; font-size: 128px; line-height: 1;
    color: var(--brand-orange); letter-spacing: -2px;
    white-space: nowrap;
  }
  .back__services {
    position: absolute; left: 0; right: 0; top: 300px;
    text-align: center;
    font-size: 24px; color: var(--brand-orange); font-weight: 400;
    letter-spacing: .5px;
  }

  /* Front card */
  .card--front { left: 60px; top: 517px; background: var(--card-dark); }
  .front__swoosh { position: absolute; inset: 0; }
  .front__brand {
    position: absolute; left: 40px; top: 26px;
    display: flex; align-items: center; gap: 18px;
  }
  .front__brand-dot {
    width: 54px; height: 54px; border-radius: 50%;
    background: var(--brand-orange);
  }
  .front__wordmark {
    font-weight: 300; font-size: 96px; line-height: 1;
    color: var(--brand-orange); letter-spacing: -1px;
    white-space: nowrap;
  }
  .front__tagline {
    position: absolute; left: 250px; top: 132px;
    font-style: italic; font-size: 17px; color: var(--text-muted);
  }
  .front__contact {
    position: absolute; left: 40px; top: 160px;
    list-style: none; font-size: 15px; color: var(--text-light);
    line-height: 26px;
  }
  .front__contact li { display: flex; align-items: center; gap: 8px; }
  .front__contact svg { width: 14px; height: 14px; flex: none; }
  .front__person {
    position: absolute; right: 40px; bottom: 22px; text-align: right;
    color: var(--text-light);
  }
  .front__name { font-weight: 700; font-size: 28px; line-height: 1.1; }
  .front__title { font-size: 20px; font-weight: 400; }
</style>
</head>
<body>
<main class="stage">

  <section class="card card--back" aria-label="Card back">
    <div class="back__wordmark">corvane.</div>
    <p class="back__services">Management • Software • Construction</p>
  </section>

  <section class="card card--front" aria-label="Card front">
    <svg class="front__swoosh" viewBox="0 0 700 400" preserveAspectRatio="none" aria-hidden="true">
      <defs>
        <linearGradient id="swoosh-gradient" x1="0" y1="0" x2="1" y2="0.3">
          <stop offset="0" stop-color="var(--grad-yellow)"/>
          <stop offset="0.3" stop-color="var(--grad-red)"/>
          <stop offset="0.65" stop-color="var(--grad-purple)"/>
          <stop offset="1" stop-color="var(--grad-teal)"/>
        </linearGradient>
      </defs>
      <path d="M0,262 C230,282 500,312 700,336 L700,400 L0,400 Z" fill="url(#swoosh-gradient)"/>
      <path d="M0,292 C220,298 380,320 450,400" fill="none" stroke="var(--card-dark)" stroke-width="5"/>
      <path d="M170,262 C360,274 560,300 700,322" fill="none" stroke="var(--brand-orange)" stroke-width="4"/>
    </svg>

    <div class="front__brand">
      <span class="front__brand-dot"></span>
      <span class="front__wordmark">corvane.</span>
    </div>
    <p class="front__tagline">...in the creation business.</p>

    <ul class="front__contact">
      <li>
        <svg viewBox="0 0 14 14"><circle cx="7" cy="7" r="6.5" fill="var(--brand-orange)"/><path d="M4.5 4 L6 5.5 L5.3 6.4 Q6.2 8 7.6 8.7 L8.5 8 L10 9.5 L9 10.5 Q5.5 10 3.5 5 Z" fill="#fff"/></svg>
        +61 0400 582 194
      </li>
      <li>
        <svg viewBox="0 0 14 14"><rect x="1" y="3" width="12" height="8.5" rx="1" fill="var(--brand-orange)"/><path d="M1.5 3.5 L7 8 L12.5 3.5" fill="none" stroke="#fff" stroke-width="1.2"/></svg>
        names@corvane.ventures
      </li>
      <li>Po Box 118 Lorwick 6104</li>
    </ul>

    <div class="front__person">
      <p class="front__name">Your Name</p>
      <p class="front__title">Title</p>
    </div>
  </section>

</main>
</body>
</html>
```